Business card design for a dynamic IT consulting company

We need a business card design for a young firm, specialized in the Telecommunications/Consulting industry. The name of the company is Quindor and Partners Business Consulting Ltd. (Short name: Quindor and Partnes)
Quindor = solve read reverse, so we aim to be uncomplicated and solution-oriented. The small pipe in our logo is also related to the word solve. So we need a new business card design, which is simple, eye catching and something non traditional (I would probably prefer a square shaped design rather than a rectangle, but open for suggestions). Attached our logo.

Target Market(s)

Usually our customers are Tier1 Telecoms providers (Q-Netra, Palorix, etc) and their executives.

Industry/Entity Type

Business

Contact Information for Business Card

Name: Bence Tolnavari
Email: b.tolnavari@quindor.hu
Web: www.quindor.hu
Mobile: +36 30 518 2769
Title: Managing Director

Optional:
Company name: Quindor and Partners Ltd.
Address: 1087 Budapest, Tolvenka str. 28/C, Hungary

Font styles to use
Other font styles liked:
• helveticaneue_medium, Prime Regular are used now.

Colors

Designer to choose colors to be used in the design.

Requirements
Must have
• I would like to have a 2 sided design.
Nice to have
• I thought if we make the logo a bit bigger (without the company name), that could go to the back with the company name below. I though, if the pipe in the logo is somehow touchable on the business card, would be nice and unique.

```html
<!DOCTYPE html>
<html lang="en">
<head>
<meta charset="utf-8">
<title>Quindor – Business Card</title>
<link rel="stylesheet" href="https://fonts.googleapis.com/css2?family=Exo+2:wght@300;400&family=Roboto:wght@400&display=swap">
<style>
  :root {
    --brand-blue: #1398d6;
    --brand-magenta: #b0288f;
    --ink-grey: #555a60;
    --paper: #ffffff;
    --backdrop: #d6d6d6;
  }
  * { box-sizing: border-box; margin: 0; padding: 0; }
  html, body { width: 1200px; height: 800px; overflow: hidden; }
  body {
    background: var(--backdrop);
    display: flex;
    align-items: center;
    justify-content: center;
    gap: 40px;
    font-family: "Roboto", Arial, sans-serif;
  }
  .card {
    position: relative;
    width: 540px;
    height: 309px;
    overflow: hidden;
    box-shadow: 0 4px 14px rgba(0,0,0,0.18);
  }
  .card--front { background: var(--paper); }
  .card--back { background: var(--brand-blue); }

  .card__wave { position: absolute; inset: 0; width: 100%; height: 100%; }

  .wordmark {
    position: absolute;
    display: flex;
    align-items: center;
    font-family: "Exo 2", sans-serif;
    font-weight: 400;
    line-height: 1;
    letter-spacing: 0.5px;
  }
  .wordmark__square { display: inline-block; flex: none; }

  .card--front .wordmark { left: 40px; top: 146px; gap: 10px; font-size: 26px; color: var(--ink-grey); }
  .card--front .wordmark__square { width: 11px; height: 11px; background: var(--brand-blue); }

  .card__divider {
    position: absolute; left: 290px; top: 34px;
    width: 1px; height: 150px; background: var(--brand-magenta);
  }

  .contact { position: absolute; left: 306px; top: 32px; color: var(--ink-grey); font-size: 10.5px; line-height: 14px; }
  .contact__name { font-family: "Exo 2", sans-serif; font-weight: 300; font-size: 17px; line-height: 20px; color: var(--brand-blue); text-transform: uppercase; letter-spacing: 0.5px; }
  .contact__title { margin-bottom: 8px; }
  .contact__company { color: var(--brand-blue); text-transform: uppercase; font-size: 10px; }
  .contact__address { margin-bottom: 8px; }
  .contact__line { display: flex; align-items: center; gap: 7px; }
  .contact__icon { width: 9px; height: 9px; fill: var(--brand-blue); flex: none; }

  .card--back .wordmark { left: 0; right: 0; top: 116px; justify-content: center; gap: 16px; font-size: 46px; color: var(--paper); }
  .card--back .wordmark__square { width: 20px; height: 20px; background: var(--paper); }
  .card__web { position: absolute; right: 30px; bottom: 26px; color: var(--paper); font-size: 12px; letter-spacing: 1px; }
</style>
</head>
<body>

  <section class="card card--front" aria-label="Front of business card">
    <svg class="card__wave" viewBox="0 0 540 309" preserveAspectRatio="none" aria-hidden="true">
      <path d="M0 296 C120 282 240 250 330 214 C420 180 480 166 540 158 L540 309 L0 309 Z" fill="var(--brand-blue)"/>
      <path d="M0 284 C115 270 235 238 325 202 C415 166 478 152 540 143 L540 150 C480 158 418 173 328 208 C238 244 118 276 0 290 Z" fill="var(--brand-magenta)"/>
    </svg>

    <div class="wordmark"><span class="wordmark__square"></span>Quindor</div>

    <div class="card__divider"></div>

    <div class="contact">
      <div class="contact__name">Bence Tolnavari</div>
      <div class="contact__title">Managing Director</div>
      <div class="contact__company">Quindor and Partners Ltd.</div>
      <div class="contact__address">1087 Budapest, Tolvenka<br>str. 28/C, Hungary</div>
      <div class="contact__line">
        <svg class="contact__icon" viewBox="0 0 24 24"><path d="M6.6 10.8a15.1 15.1 0 0 0 6.6 6.6l2.2-2.2a1 1 0 0 1 1-.25 11.4 11.4 0 0 0 3.6.57 1 1 0 0 1 1 1V20a1 1 0 0 1-1 1A17 17 0 0 1 3 4a1 1 0 0 1 1-1h3.5a1 1 0 0 1 1 1c0 1.25.2 2.45.57 3.57a1 1 0 0 1-.25 1z"/></svg>
        <span>+36 30 518 2769</span>
      </div>
      <div class="contact__line">
        <svg class="contact__icon" viewBox="0 0 24 24"><path d="M2 5h20v2l-10 6L2 7z M2 9l10 6 10-6v10H2z"/></svg>
        <span>b.tolnavari@quindor.hu</span>
      </div>
      <div class="contact__line">
        <svg class="contact__icon" viewBox="0 0 24 24"><circle cx="12" cy="12" r="10"/></svg>
        <span>www.quindor.hu</span>
      </div>
    </div>
  </section>

  <section class="card card--back" aria-label="Back of business card">
    <div class="wordmark"><span class="wordmark__square"></span>Quindor</div>
    <div class="card__web">www.quindor.hu</div>
  </section>

</body>
</html>
```